Velmo Swinger site - new website, blogsite and merchandise point, connection to tradeva

We are a well established Swingers Club in the North east of UK and already have an existing site. www.velmo-example.co.uk, BUT we have changed our logo and our information on the site needs to be updated.

We are changing our hosting site to Nimbrashost.example ,also wanting to start a blog which is linked to the club, plus we wish to sell a small exclusive range of Velmo linked merchandise which will also be available on Tradeva.

I have attached a pdf of the majority of the content. additionally we will provide pictures and a videoclip which should be able to be viewed by pc's, lap tops and mobile phones (the whole website must be fully accessible via phone).

The new site must be able to be updated by someone with medium computer knowledge (usually me), by no means expert. Updates will generally be new pictures and written information. The site must be able to be transferred to NimbrasHost.

Velmo is one of the countries leading clubs and emphasises friendliness, fun & safety for its members, we look after you to ensure your experience is the best we can offer. We are very proud of our reputation, built up over more than 10 years.

Target Market(s)

Swingers, dreamers & fantasists, alternative lifestyle people

Coding

Coded - Design and coding required

Number of Pages Required

5+ page

Font styles to use
Sans Serif

Colors
000000
ec1f27
fbfbfb
eeeeee
eaeaea

Requirements
Must have
• website with blog attached, link to tradeva & quidlo, ability to run videoclip and picture album and must be compatable to transfer easily to Nimbrashost and be updated by non-professional (who can learn)
• Straightforward & easy to navigate
• over 18 content page with enter button
Nice to have
• sexy site
• link to chirpster maybe
• black site would be nice with red or white writing
Should not have
• children and animals in anyway shape or form

```html
<!DOCTYPE html>
<html lang="en">
<head>
<meta charset="utf-8">
<title>Velmo – Swingers Club</title>
<link href="https://fonts.googleapis.com/css2?family=Open+Sans:wght@300;400;600;700;800&display=swap" rel="stylesheet">
<style>
:root{
  --black:#000000;
  --red:#ec1f27;
  --white:#fbfbfb;
  --light:#eeeeee;
  --soft:#eaeaea;
  --panel:#181818;
  --card:#1c1c1c;
  --footer:#111111;
  --muted:#b5b5b5;
}
*{margin:0;padding:0;box-sizing:border-box}
html,body{width:1200px;height:3991px;overflow:hidden;background:var(--black)}
body{position:relative;font-family:"Open Sans",Arial,sans-serif;color:var(--white)}
.abs{position:absolute}
.section-title{position:absolute;left:0;width:1200px;text-align:center;color:var(--red);font-size:24px;font-weight:600}
.btn-outline{position:absolute;border:2px solid var(--red);color:var(--red);font-size:11px;font-weight:600;text-transform:uppercase;display:flex;align-items:center;justify-content:center;letter-spacing:.5px}
.photo{position:absolute}

/* header */
.site-header{position:absolute;left:0;top:0;width:1200px;height:125px;background:var(--black)}
.logo{position:absolute;display:flex;align-items:center;gap:8px;font-weight:300;color:var(--white);letter-spacing:3px}
.logo .mark{width:10px;height:10px;background:var(--red)}
.phone{position:absolute;left:862px;top:26px;display:flex;align-items:center;gap:10px;font-size:13px}
.phone .num{color:var(--red);font-size:19px;font-weight:600}
.main-nav{position:absolute;left:434px;top:70px;display:flex;gap:30px;font-size:13px}
.main-nav a{color:var(--white);text-decoration:none;padding:5px 0}
.main-nav a.active{background:var(--red);padding:5px 14px}

/* hero */
.hero{position:absolute;left:0;top:125px;width:1200px;height:561px;background:linear-gradient(120deg,#2b2b2b,#6a6a6a 45%,#3a3a3a 75%,#1e1e1e)}
.hero-title{position:absolute;left:0;top:190px;width:1200px;text-align:center;font-size:50px;font-weight:700}
.hero-sub{position:absolute;left:0;top:256px;width:1200px;text-align:center;font-size:17px;font-weight:600}
.hero-btn{position:absolute;left:492px;top:295px;width:213px;height:59px;background:var(--red);display:flex;align-items:center;justify-content:center;font-size:17px;font-weight:700}
.dots{position:absolute;left:546px;top:502px;display:flex;gap:14px}
.dots span{width:9px;height:9px;border-radius:50%;background:var(--white)}
.dots span.on{background:transparent;border:2px solid var(--white)}

/* pricing */
.price-card{position:absolute;top:828px;width:229px;height:215px;background:var(--card);text-align:center;padding:28px 14px 0}
.price-card h3{font-size:17px;font-weight:600;margin-bottom:12px}
.price-card p{font-size:12px;color:var(--muted);line-height:1.6;margin-bottom:10px}
.price-card em{font-style:normal;color:var(--red)}

.intro p{position:absolute;left:300px;width:600px;text-align:center;font-size:12px;color:var(--muted);line-height:1.75}

.gallery-item{position:absolute;top:1373px;width:222px;height:165px}
.gallery-label{position:absolute;top:1552px;width:222px;text-align:center;font-size:12px;color:var(--muted)}
.arrow{position:absolute;top:1440px}

.sell-btn{position:absolute;left:380px;top:1618px;width:440px;height:64px;background:var(--red);display:flex;align-items:center;justify-content:center;gap:14px;font-size:25px;font-weight:800}
.sell-btn .badge{font-size:20px;font-weight:800}

.product-img{position:absolute;top:1841px;width:186px;height:203px;background:var(--white);display:flex;align-items:center;justify-content:center}
.product-name{position:absolute;top:2072px;width:186px;text-align:center;font-size:14px;font-weight:600}
.product-price{position:absolute;top:2098px;width:186px;text-align:center;font-size:19px;font-weight:700}

.blog-img{position:absolute;top:2339px;height:189px}
.blog-title{position:absolute;top:2563px;font-size:17px;font-weight:700;line-height:1.3}
.blog-text{position:absolute;font-size:12px;color:var(--muted);line-height:1.6}

.panel{position:absolute;left:128px;width:944px;background:var(--panel)}
.panel h2{position:absolute;color:var(--red);font-size:22px;font-weight:600}
.panel p{position:absolute;font-size:12px;color:var(--muted);line-height:1.6}

.site-footer{position:absolute;left:0;top:3667px;width:1200px;height:324px;background:var(--footer)}
.footer-divider{position:absolute;left:393px;top:3743px;width:1px;height:72px;background:#444}
.follow{position:absolute;left:446px;top:3742px;display:flex;align-items:center;gap:10px;font-size:11px;color:var(--muted)}
.follow .dot{width:18px;height:18px;border-radius:50%}
.footer-links{position:absolute;left:446px;top:3795px;display:flex;gap:12px;font-size:11px;color:var(--muted)}
.footer-rule{position:absolute;left:128px;top:3872px;width:944px;height:1px;background:#333}
.copyright{position:absolute;left:0;top:3922px;width:1200px;text-align:center;font-size:11px;color:var(--muted)}
</style>
</head>
<body>

<header class="site-header">
  <div class="logo" style="left:128px;top:22px;font-size:48px">VELMO<span class="mark"></span></div>
  <div class="phone">
    <svg width="14" height="14" viewBox="0 0 24 24"><path fill="#fbfbfb" d="M6.6 10.8a15.1 15.1 0 0 0 6.6 6.6l2.2-2.2c.3-.3.7-.4 1-.2 1.1.4 2.3.6 3.6.6.6 0 1 .4 1 1V20c0 .6-.4 1-1 1A17 17 0 0 1 3 4c0-.6.4-1 1-1h3.5c.6 0 1 .4 1 1 0 1.3.2 2.5.6 3.6.1.3 0 .7-.2 1z"/></svg>
    <span>By phone</span><span class="num">0790 0123456</span>
  </div>
  <nav class="main-nav">
    <a class="active">Home</a><a>Diary</a><a>Theme Parties</a><a>TV/TG and Admirers</a><a>Membership</a><a>Rooms</a><a>Contact US</a>
  </nav>
</header>

<section class="hero">
  <div class="photo" role="img" aria-label="Group of smiling adults raising wine glasses at the club bar" style="inset:0;background:linear-gradient(120deg,#2a2a2a,#767676 40%,#4a4a4a 70%,#1c1c1c)"></div>
  <h1 class="hero-title">Swingers Club</h1>
  <p class="hero-sub">we have to increase some of our charges</p>
  <a class="hero-btn">READ MORE</a>
  <div class="dots"><span></span><span class="on"></span><span></span><span></span><span></span></div>
</section>

<h2 class="section-title" style="top:748px">Pricing</h2>
<div class="price-card" style="left:128px"><h3>Crash</h3><p>will be <em>£16</em> per person</p><p>(places allocated first come, first served @ 1.40am)</p></div>
<div class="price-card" style="left:367px"><h3>Corkage</h3><p>will be <em>£1</em> per person</p><p>( we will now have available lemons &amp; limes)</p></div>
<div class="price-card" style="left:605px"><h3>Some entry fees</h3><p>Friday nights <em>£22</em> (couples &amp; single guys) Single ladies <em>£5</em></p><p>Saturday nights (couples) <em>£25</em> entry, Single ladies <em>£10</em></p></div>
<div class="price-card" style="left:843px"><h3>10 couple entry vouchers</h3><p><em>£200</em> valid for any night</p><p><em>£175</em> valid for Fridays</p><p><em>£100</em> valid for Wednesdays</p></div>

<h2 class="section-title" style="top:1116px">A Great Place To Meet And Play!</h2>
<div class="intro">
  <p style="top:1172px">We are the best Swingers Club in the North East, and also voted No 2 club in the UK.</p>
  <p style="top:1205px">We have retained the coveted title of No 1 friendliest club in the UK (in joint 1st place with our great friends "Night Harbour", London).</p>
</div>
<a class="btn-outline" style="left:543px;top:1290px;width:114px;height:35px">Read more</a>

<svg class="arrow" style="left:96px" width="16" height="30" viewBox="0 0 16 30"><path d="M14 2 2 15l12 13" fill="none" stroke="#888" stroke-width="2"/></svg>
<svg class="arrow" style="left:1088px" width="16" height="30" viewBox="0 0 16 30"><path d="M2 2l12 13L2 28" fill="none" stroke="#888" stroke-width="2"/></svg>
<div class="gallery-item" role="img" aria-label="Indoor hot tub room" style="left:128px;background:linear-gradient(160deg,#8a8a4a,#b0a870 50%,#5b5a30)"></div>
<div class="gallery-item" role="img" aria-label="Wooden sauna interior" style="left:369px;background:linear-gradient(160deg,#8b4a20,#c0783a 50%,#5a2c10)"></div>
<div class="gallery-item" role="img" aria-label="Steam room with tiled seating" style="left:609px;background:linear-gradient(160deg,#5a3a3a,#9a6a6a 50%,#3a2020)"></div>
<div class="gallery-item" role="img" aria-label="Red lit playroom" style="left:850px;background:linear-gradient(160deg,#6a1018,#c0303a 50%,#3a0508)"></div>
<div class="gallery-label" style="left:128px">Hot tub</div>
<div class="gallery-label" style="left:369px">Sauna</div>
<div class="gallery-label" style="left:609px">Steam Room</div>
<div class="gallery-label" style="left:850px">Playrooms</div>

<a class="sell-btn">SELL VELMO <span class="badge">Tradeva</span></a>

<h2 class="section-title" style="top:1749px">Products</h2>
<div class="product-img" style="left:141px"><div role="img" aria-label="Blue t-shirt" style="width:130px;height:170px;background:linear-gradient(#2a5bd0,#1a3f9a)"></div></div>
<div class="product-img" style="left:383px"><div role="img" aria-label="Black t-shirt" style="width:130px;height:170px;background:linear-gradient(#222,#050505)"></div></div>
<div class="product-img" style="left:639px"><div role="img" aria-label="Paper coffee cup" style="width:80px;height:150px;background:linear-gradient(#eee,#8a6a4a 40%,#ddd)"></div></div>
<div class="product-img" style="left:883px"><div role="img" aria-label="White mug" style="width:110px;height:110px;background:linear-gradient(#fff,#d8d8d8)"></div></div>
<div class="product-name" style="left:141px">Lorem ipsuem</div><div class="product-price" style="left:141px">$99.99</div>
<div class="product-name" style="left:383px">Contrary to pop</div><div class="product-price" style="left:383px">$49.99</div>
<div class="product-name" style="left:639px">There are many var</div><div class="product-price" style="left:639px">$19.99</div>
<div class="product-name" style="left:883px">Lorem ipsuem</div><div class="product-price" style="left:883px">$39.99</div>
<a class="btn-outline" style="left:183px;top:2145px;width:102px;height:35px">Shop now</a>
<a class="btn-outline" style="left:425px;top:2145px;width:102px;height:35px">Shop now</a>
<a class="btn-outline" style="left:681px;top:2145px;width:102px;height:35px">Shop now</a>
<a class="btn-outline" style="left:925px;top:2145px;width:102px;height:35px">Shop now</a>

<h2 class="section-title" style="top:2252px">Latest Blog</h2>
<div class="blog-img" role="img" aria-label="Club interior with red lighting and wooden wheel" style="left:128px;width:300px;background:linear-gradient(150deg,#c04020,#6a2010 55%,#2a0a05)"></div>
<div class="blog-img" role="img" aria-label="Red curtained private booth" style="left:452px;width:298px;background:linear-gradient(150deg,#d01820,#7a0a10 60%,#3a0508)"></div>
<div class="blog-img" role="img" aria-label="Hotel style bedroom with twin beds" style="left:772px;width:295px;background:linear-gradient(150deg,#6a5a4a,#c0a080 50%,#3a2a20)"></div>
<h3 class="blog-title" style="left:128px;width:300px">Where are you based?</h3>
<h3 class="blog-title" style="left:452px;width:298px">Will I have to give my name<br>&amp; address?</h3>
<h3 class="blog-title" style="left:772px;width:295px">Do we have to "do anything"?</h3>
<p class="blog-text" style="left:128px;top:2600px;width:290px">We are 6 miles from J63 of the M90, in Brackton in County Elmshire, we are very easy to find but please don't...</p>
<p class="blog-text" style="left:452px;top:2626px;width:290px">Yes, but don't worry. Your personal information is kept absolutely confidential.</p>
<p class="blog-text" style="left:772px;top:2600px;width:290px">If you just want to stay together or maybe have a chat with someone and use the facilities that's not a problem.</p>
<a class="btn-outline" style="left:140px;top:2685px;width:114px;height:35px">Read more</a>
<a class="btn-outline" style="left:460px;top:2685px;width:114px;height:35px">Read more</a>
<a class="btn-outline" style="left:778px;top:2685px;width:114px;height:35px">Read more</a>

<section class="panel" style="top:2805px;height:303px">
  <div role="img" aria-label="Woman in a gold sequined dress among falling confetti" style="position:absolute;left:24px;top:21px;width:354px;height:261px;background:linear-gradient(135deg,#e8a0b8,#d4708f 45%,#c8a040 60%,#e8a0b8)"></div>
  <h2 style="left:418px;top:28px">Dress</h2>
  <p style="left:418px;top:80px;width:500px">Smart casual, no hoodies and caps please!</p>
  <p style="left:418px;top:112px;width:500px">Saturdays is a smart night out and people dress to impress.</p>
  <p style="left:418px;top:144px;width:500px">Wear what you would wear on a night out and bring lingerie, basques, rubber etc to change into if you feel you want to dress down a bit.</p>
  <p style="left:418px;top:195px;width:500px">Guys – dress to impress, remember ripped jeans on a Saturday night just don't look the part.</p>
  <p style="left:418px;top:246px;width:500px">Ladies – sexy or demure – whatever you wear, you will always look lovely.</p>
</section>

<section class="panel" style="top:3148px;height:450px">
  <h2 style="left:48px;top:58px">Alcohol</h2>
  <p style="left:48px;top:118px;width:480px">Please bring your own alcoholic drinks, which we will put behind the bar (chilled as necessary) and serve to you.</p>
  <p style="left:48px;top:180px;width:480px">We do charge a corkage charge to help towards our bar staff costs, glasses, ice, lemons &amp; limes etc, this charge is a nominal £1 charge per person, per evening (NOT per bottle or can).</p>
  <p style="left:48px;top:262px;width:480px">We ask that you buy your soft drinks/tea/coffee etc from us.</p>
  <div role="img" aria-label="Two glasses of beer clinking together" style="position:absolute;left:559px;top:21px;width:359px;height:405px;background:radial-gradient(circle at 50% 60%,#e09030,#8a4a10 50%,#1a1a2a)"></div>
</section>

<footer class="site-footer"></footer>
<div class="logo" style="left:128px;top:3745px;font-size:48px">VELMO<span class="mark"></span></div>
<div class="footer-divider"></div>
<div class="follow">FOLLOW US ON :
  <span class="dot" style="background:#3b5998"></span><span class="dot" style="background:#1da1f2"></span><span class="dot" style="background:#dd4b39"></span>
</div>
<nav class="footer-links"><span>Home</span>|<span>Diary</span>|<span>Theme Parties</span>|<span>TV/TG and Admirers</span>|<span>Membership</span>|<span>FAQs</span>|<span>Rooms</span>|<span>Contact US</span>|<span>Links</span></nav>
<div class="footer-rule"></div>
<p class="copyright">Copyright @ 2017 All Rights Reserved</p>

</body>
</html>
```